Home Staging Company needs business card design

We're a home staging company called Brightly Settled Home Staging. We would like a business card design that includes aqua and gray. Our current logo of house within chair is fine but I find we almost always use the logo in one color. I'll upload images of front and back of our current card and our logo. Note that we have dropped "Solutions" from our company name and don't want to include it on the card.

Target Market(s)

Realtors and homeowners - people interested in selling their homes

Contact Information for Business Card

Marisol Thistlewood
Brightly Settled Home Staging
757-555-0193
www.brightlysettled.com
marisol@brightlysettled.com

Font styles to use
Serif
Script

Requirements
Must have
• My logo and contact details
• UPDATE***
• I forgot to say that the company name should be included on the front of the card somehow.

```html
<!DOCTYPE html>
<html lang="en">
<head>
<meta charset="utf-8">
<title>Brightly Settled Home Staging – Business Card</title>
<link href="https://fonts.googleapis.com/css2?family=Roboto+Condensed:wght@400&family=Questrial&display=swap" rel="stylesheet">
<style>
  :root {
    --backdrop: #d6d6d6;
    --aqua: #4ba9b3;
    --aqua-deep: #3f9aa4;
    --charcoal: #373b3f;
    --ink: #15262a;
    --paper-light: #e9ecec;
    --card-shadow: rgba(0, 0, 0, 0.28);
  }
  * { box-sizing: border-box; margin: 0; padding: 0; }
  html, body {
    width: 1200px;
    height: 576px;
    overflow: hidden;
    background: var(--backdrop);
  }
  .canvas {
    position: relative;
    width: 1200px;
    height: 576px;
  }
  .card {
    position: absolute;
    top: 138px;
    width: 484px;
    height: 294px;
    border-radius: 14px;
    box-shadow: 2px 4px 8px var(--card-shadow);
    overflow: hidden;
  }
  .card--front {
    left: 82px;
    background: linear-gradient(180deg, var(--aqua) 0%, var(--aqua-deep) 100%);
    color: var(--ink);
  }
  .card--back {
    left: 602px;
    background: var(--charcoal);
    color: var(--paper-light);
  }
  .holder-name {
    position: absolute;
    left: 26px;
    top: 34px;
    font-family: "Roboto Condensed", sans-serif;
    font-size: 19px;
    letter-spacing: 0.2px;
  }
  .holder-title {
    position: absolute;
    left: 26px;
    top: 61px;
    font-family: "Questrial", sans-serif;
    font-size: 11px;
  }
  .contact-list {
    position: absolute;
    left: 26px;
    top: 100px;
    list-style: none;
    font-family: "Questrial", sans-serif;
    font-size: 12px;
  }
  .contact-item {
    display: flex;
    align-items: center;
    height: 17px;
  }
  .contact-icon {
    width: 11px;
    height: 11px;
    margin-right: 13px;
    fill: var(--ink);
  }
  .brand {
    position: absolute;
    display: flex;
    align-items: center;
    gap: 10px;
    font-family: "Questrial", sans-serif;
    font-size: 15px;
    line-height: 1.15;
  }
  .brand-mark {
    width: 30px;
    height: 30px;
    border-radius: 50%;
    flex: none;
  }
  .card--front .brand {
    left: 26px;
    top: 238px;
    color: var(--ink);
  }
  .card--front .brand-mark { background: var(--ink); }
  .card--back .brand {
    right: 46px;
    top: 236px;
    color: var(--paper-light);
  }
  .card--back .brand-mark { background: var(--aqua); }
</style>
</head>
<body>
<main class="canvas">
  <section class="card card--front" aria-label="Business card front">
    <h1 class="holder-name">Marisol Thistlewood</h1>
    <p class="holder-title">Managing Director</p>
    <ul class="contact-list">
      <li class="contact-item">
        <svg class="contact-icon" viewBox="0 0 12 12" aria-hidden="true"><path d="M1 3.5C1 2 3 1.5 6 1.5S11 2 11 3.5V5H8.5V3.8H3.5V5H1Z"/><path d="M2.5 6.2 4 4.8h4l1.5 1.4V10.5h-7Z"/></svg>
        <span>757-555-0193</span>
      </li>
      <li class="contact-item">
        <svg class="contact-icon" viewBox="0 0 12 12" aria-hidden="true"><circle cx="6" cy="6" r="5" fill="none" stroke="#15262a" stroke-width="1.2"/><path d="M1 6h10M6 1c-2.5 3-2.5 7 0 10M6 1c2.5 3 2.5 7 0 10" fill="none" stroke="#15262a" stroke-width="1"/></svg>
        <span>www.brightlysettled.com</span>
      </li>
      <li class="contact-item">
        <svg class="contact-icon" viewBox="0 0 12 12" aria-hidden="true"><path d="M0.5 2.5h11v7h-11Z"/><path d="M0.8 2.8 6 6.8l5.2-4" fill="none" stroke="#4ba9b3" stroke-width="1"/></svg>
        <span>marisol@brightlysettled.com</span>
      </li>
    </ul>
    <div class="brand">
      <span class="brand-mark" aria-hidden="true"></span>
      <span class="brand-name">Brightly Settled<br>Home Staging</span>
    </div>
  </section>

  <section class="card card--back" aria-label="Business card back">
    <div class="brand">
      <span class="brand-mark" aria-hidden="true"></span>
      <span class="brand-name">Brightly Settled<br>Home Staging</span>
    </div>
  </section>
</main>
</body>
</html>
```